Grey Fennel Medical Website to make connecting and communicating easier

To create a unique, user-friendly, professional website for patients and professionals to access education/ information, forms, appointments, contact details, and data about us, and for us to have the capacity to link to various cloud-based platforms.
To use the logo design and colour scheme we have just sourced.

WEBSITE to be eye catching, Inspiring and alluring
- efficient and logical
- professional and trustworthy appearance
- health focus "living health matters"
- user friendly
- ability to link with cloud-based software and video conferencing tools/ telehealth
- colours- black/ white teal and ?silver

PAGES:
page 1 - Our clinic and staff, services offered, contact us- address/ map / contact details- social media connections
page 2- patients and visitors - New patient forms to complete, news and patient informtion (educatinal)
page 3 - health professionals -referral forms, research and education
page 3- online appointments
page 4 - Quick links - partners, other services
page 5- privacy policy, disclaimer

HI, Could we please extend the deadline another 5 days, so sorry just struggling with my workload to be able to keep up and I am wanting to liaise more with the designer that I will choose. I am so happy with SketchHarbor and all the designers - thank you! Thank you so much!!

Target Market(s)

Patients - mostly over 60's so the website must be minimal clicks and simple to navigate
Professionals - for education and access forms

Industry/Entity Type

Health Care

Coding

Coded - Design and coding required

Number of Pages Required

5+ page

Font styles to use
Sans Serif
Script

Colors
33b8a4
86cfc6

Requirements
Must have
• WEBSITE to be eye catching, Inspiring and alluring
- efficient and logical
- user friendly

WEBSITE - professional and user friendly
- ability to link with cloud based software and videoconferencing/ telehealth
Nice to have
• clean and crisp presentation
happy for an innovative look
room to add more services and ability to link pages and resources
Should not have
• Please ensure the website is not:
clunky
difficult to navigate
common and cheap looking

```html
<!DOCTYPE html>
<html lang="en">
<head>
<meta charset="utf-8">
<title>Grey Fennel Medical – Patients And Visitors</title>
<link href="https://fonts.googleapis.com/css2?family=Comfortaa:wght@400;500&family=Montserrat:wght@400;500;600;700&display=swap" rel="stylesheet">
<style>
:root{
  --teal:#33b8a4;
  --teal-deep:#119284;
  --teal-soft:#86cfc6;
  --ink:#111111;
  --text:#333333;
  --muted:#777777;
  --line:#cfcfcf;
  --grey-band:#f2f2f2;
  --white:#ffffff;
  --black:#000000;
  --pdf-red:#e0262b;
}
*{box-sizing:border-box;margin:0;padding:0}
html,body{width:1200px;height:3284px;overflow:hidden;background:var(--white)}
body{font-family:'Montserrat',sans-serif;color:var(--text);position:relative}
.display{font-family:'Comfortaa',sans-serif;font-weight:500;color:var(--ink);letter-spacing:1px}

/* header */
.site-header{position:absolute;left:0;top:0;width:1200px;height:90px;background:var(--white)}
.brand{position:absolute;left:182px;top:30px;display:flex;align-items:center;gap:8px;font-weight:700;font-size:15px;color:var(--teal)}
.brand-dot{width:22px;height:22px;border-radius:50%;background:var(--teal)}
.main-nav a{position:absolute;top:40px;font-size:15px;color:#444;text-decoration:none}
.social-circle{position:absolute;border-radius:50%;background:var(--teal-soft)}
.site-header .social-circle{top:32px;width:32px;height:32px}

/* hero */
.hero{position:absolute;left:0;top:90px;width:1200px;height:375px;background:var(--teal-deep);overflow:hidden}
.hero-art{position:absolute}
.hero-title{position:absolute;left:0;width:1200px;top:158px;text-align:center;font-family:'Comfortaa',sans-serif;font-size:46px;font-weight:400;color:var(--white);letter-spacing:2px}

/* section headings */
.section-title{position:absolute;left:0;width:1200px;text-align:center;font-size:38px}
.title-rule{position:absolute;left:581px;width:38px;height:2px;background:var(--teal)}

/* form */
.field{position:absolute;height:46px;border:1px solid #bbb;border-radius:23px;display:flex;align-items:center;padding-left:24px;font-size:12.5px;color:#444;gap:9px}
.field svg{flex:none}
.field.textarea{border-radius:6px;align-items:flex-start;padding-top:15px;height:186px}
.btn-pill{position:absolute;height:46px;width:227px;left:486px;border-radius:23px;background:var(--teal);color:var(--white);font-weight:600;font-size:16px;display:flex;align-items:center;justify-content:center}

/* blogs */
.blogs-band{position:absolute;left:0;top:1186px;width:1200px;height:1038px;background:var(--grey-band)}
.blog-card{position:absolute;width:262px;height:353px;background:var(--white)}
.blog-media{height:185px;width:100%}
.blog-card h3{position:absolute;left:23px;top:212px;font-size:16px;font-weight:700;color:var(--ink);white-space:nowrap}
.blog-card p{position:absolute;left:23px;top:238px;width:225px;font-size:12px;line-height:19px;color:var(--muted)}
.read-more{position:absolute;left:23px;top:305px;font-size:12px;font-weight:600;color:var(--teal);display:flex;align-items:center;gap:6px}

/* education */
.edu-item{position:absolute;left:232px;width:734px;height:135px;border:1px solid #d8d8d8;background:var(--white);box-shadow:0 2px 4px rgba(0,0,0,.05)}
.edu-icon{position:absolute;left:38px;top:22px}
.edu-divider{position:absolute;top:50px;width:1px;height:32px;background:var(--line)}
.edu-date{position:absolute;left:176px;top:27px;font-size:11.5px;font-style:italic;color:var(--teal);display:flex;gap:5px;align-items:center}
.edu-item h4{position:absolute;left:176px;top:50px;font-size:17px;font-weight:600;color:var(--ink);white-space:nowrap}
.edu-item p{position:absolute;left:176px;top:80px;width:330px;font-size:10px;line-height:16px;color:var(--muted)}
.edu-btn{position:absolute;left:571px;width:125px;height:32px;border-radius:16px;color:var(--white);font-size:11px;font-weight:600;display:flex;align-items:center;justify-content:center}
.edu-btn.primary{top:28px;background:var(--teal)}
.edu-btn.secondary{top:75px;background:var(--teal-soft)}

/* footer */
.site-footer{position:absolute;left:0;top:2915px;width:1200px;height:369px;background:var(--black);color:var(--white)}
.footer-brand{position:absolute;left:191px;top:118px;display:flex;align-items:center;gap:8px;font-weight:700;font-size:15px;color:var(--teal)}
.lang-select{position:absolute;left:184px;top:201px;width:139px;height:34px;border:1px solid #ddd;display:flex;align-items:center;padding:0 12px 0 26px;font-size:11px;justify-content:space-between}
.footer-heading{position:absolute;font-size:16px;font-weight:700}
.footer-rule{position:absolute;width:20px;height:2px;background:var(--teal)}
.footer-links li{list-style:none;position:absolute;left:390px;font-size:11.5px}
.contact-row{position:absolute;left:560px;display:flex;gap:12px;font-size:10px;line-height:14px}
.contact-row b{font-weight:700}
.site-footer .social-circle{top:123px;width:34px;height:34px;background:var(--teal)}
.footer-base{position:absolute;left:184px;top:313px;width:832px;height:1px;background:#333}
.copyright{position:absolute;top:337px;font-size:11px}
</style>
</head>
<body>

<header class="site-header">
  <div class="brand"><span class="brand-dot"></span>Grey Fennel Medical</div>
  <nav class="main-nav">
    <a style="left:498px">Home</a>
    <a style="left:584px">Staff</a>
    <a style="left:658px">Services</a>
    <a style="left:758px">Contact Us</a>
  </nav>
  <span class="social-circle" style="left:862px" aria-label="Social link 1"></span>
  <span class="social-circle" style="left:903px" aria-label="Social link 2"></span>
  <span class="social-circle" style="left:944px" aria-label="Social link 3"></span>
  <span class="social-circle" style="left:985px" aria-label="Social link 4"></span>
</header>

<section class="hero">
  <div class="hero-art" role="img" aria-label="Illustration of a nurse pushing an elderly patient in a wheelchair" style="left:38px;top:25px;width:296px;height:344px;border-radius:40% 40% 6px 6px;background:linear-gradient(180deg,#3a86c9 0%,#2f6fa8 100%);opacity:.55"></div>
  <div class="hero-art" role="img" aria-label="Faint illustration of medical staff in the background" style="left:363px;top:105px;width:96px;height:215px;border-radius:30px;background:#2a9f8f;opacity:.6"></div>
  <div class="hero-art" role="img" aria-label="Illustration of a nurse beside a patient resting in a hospital bed" style="left:848px;top:55px;width:325px;height:320px;border-radius:24px 24px 0 0;background:linear-gradient(180deg,#c9d6dc 0%,#9aa6ac 100%);opacity:.55"></div>
  <h1 class="hero-title">Patients And Visitors</h1>
</section>

<section class="register">
  <h2 class="section-title display" style="top:530px">Patient?, Get Register here...</h2>
  <span class="title-rule" style="top:595px"></span>

  <div class="field" style="left:232px;top:635px;width:356px">
    <svg width="13" height="14" viewBox="0 0 13 14"><circle cx="6.5" cy="4" r="3.5" fill="#555"/><path d="M0 14c0-4 3-6 6.5-6S13 10 13 14z" fill="#555"/></svg>First Name*</div>
  <div class="field" style="left:612px;top:635px;width:356px">
    <svg width="13" height="14" viewBox="0 0 13 14"><circle cx="6.5" cy="4" r="3.5" fill="#555"/><path d="M0 14c0-4 3-6 6.5-6S13 10 13 14z" fill="#555"/></svg>Last Name*</div>
  <div class="field" style="left:232px;top:704px;width:356px">
    <svg width="14" height="13" viewBox="0 0 14 13"><rect x="0.5" y="2" width="13" height="10.5" fill="none" stroke="#555"/><rect x="0.5" y="2" width="13" height="3" fill="#555"/><path d="M3 7h2M6 7h2M9 7h2M3 9.5h2M6 9.5h2M9 9.5h2" stroke="#555"/></svg>Date of birth</div>
  <div class="field" style="left:612px;top:704px;width:356px">
    <svg width="15" height="14" viewBox="0 0 15 14"><circle cx="5.5" cy="4" r="3.5" fill="#555"/><path d="M0 14c0-4 2.5-6 5.5-6 2 0 3 1 3.5 2" fill="#555"/><circle cx="11" cy="10" r="2.5" fill="none" stroke="#555" stroke-width="1.3"/></svg>Concern*
    <svg style="position:absolute;right:28px" width="10" height="6" viewBox="0 0 10 6"><path d="M0 0h10L5 6z" fill="#444"/></svg></div>
  <div class="field" style="left:232px;top:771px;width:356px">
    <svg width="9" height="15" viewBox="0 0 9 15"><rect x="0.7" y="0.7" width="7.6" height="13.6" rx="1.5" fill="none" stroke="#555" stroke-width="1.3"/><circle cx="4.5" cy="12" r=".9" fill="#555"/></svg>Phone Number*</div>
  <div class="field" style="left:612px;top:771px;width:356px">
    <svg width="15" height="11" viewBox="0 0 15 11"><rect width="15" height="11" fill="#555"/><path d="M0 0l7.5 6L15 0" fill="none" stroke="#fff" stroke-width="1.2"/></svg>Email Address*</div>
  <div class="field textarea" style="left:232px;top:840px;width:736px">
    <svg width="15" height="14" viewBox="0 0 15 14"><path d="M1 1h10v7H5l-3 3V8H1z" fill="none" stroke="#555" stroke-width="1.3"/><path d="M12 4h2v6h-1v2l-2-2H7" fill="none" stroke="#555" stroke-width="1.3"/></svg>Tell us About your problem in detail...</div>

  <div class="btn-pill" style="top:1066px">See All Our Services</div>
</section>

<section class="blogs-band">
  <h2 class="section-title display" style="top:65px">Blogs For Patients</h2>

  <article class="blog-card" style="left:185px;top:148px">
    <div class="blog-media" role="img" aria-label="Illustration of a family wearing face masks" style="background:linear-gradient(135deg,#d7e3fb,#b9cdf5)"></div>
    <h3>Lorem Ipsum Door Sit...</h3>
    <p>Lorem ipsum dolor sit amet, consec-tetur adipiscing elit, sed do eiusmod tempor incididunt ut labore et...</p>
    <span class="read-more">Read More <svg width="13" height="8" viewBox="0 0 13 8"><path d="M0 4h11M8 1l3 3-3 3" fill="none" stroke="#33b8a4" stroke-width="1.4"/></svg></span>
  </article>
  <article class="blog-card" style="left:469px;top:148px">
    <div class="blog-media" role="img" aria-label="Illustration of a group of office workers in masks" style="background:linear-gradient(180deg,#9fd6de,#3c4f7c)"></div>
    <h3>Lorem Ipsum Door Sit...</h3>
    <p>Lorem ipsum dolor sit amet, consec-tetur adipiscing elit, sed do eiusmod tempor incididunt ut labore et...</p>
    <span class="read-more">Read More <svg width="13" height="8" viewBox="0 0 13 8"><path d="M0 4h11M8 1l3 3-3 3" fill="none" stroke="#33b8a4" stroke-width="1.4"/></svg></span>
  </article>
  <article class="blog-card" style="left:753px;top:148px">
    <div class="blog-media" role="img" aria-label="Illustration of a surgical team in an operating room" style="background:linear-gradient(180deg,#eef3fb,#d6e2f3)"></div>
    <h3>Lorem Ipsum Door Sit...</h3>
    <p>Lorem ipsum dolor sit amet, consec-tetur adipiscing elit, sed do eiusmod tempor incididunt ut labore et...</p>
    <span class="read-more">Read More <svg width="13" height="8" viewBox="0 0 13 8"><path d="M0 4h11M8 1l3 3-3 3" fill="none" stroke="#33b8a4" stroke-width="1.4"/></svg></span>
  </article>

  <article class="blog-card" style="left:185px;top:524px">
    <div class="blog-media" role="img" aria-label="Medical graphic of a heart with a pulse line" style="background:linear-gradient(135deg,#6fc6dc,#b7e0ea)"></div>
    <h3>Lorem Ipsum Door Sit...</h3>
    <p>Lorem ipsum dolor sit amet, consec-tetur adipiscing elit, sed do eiusmod tempor incididunt ut labore et...</p>
    <span class="read-more">Read More <svg width="13" height="8" viewBox="0 0 13 8"><path d="M0 4h11M8 1l3 3-3 3" fill="none" stroke="#33b8a4" stroke-width="1.4"/></svg></span>
  </article>
  <article class="blog-card" style="left:469px;top:524px">
    <div class="blog-media" role="img" aria-label="Illustration of people handling oversized medicine packages" style="background:linear-gradient(180deg,#f3f5fb,#e2e7f3)"></div>
    <h3>Lorem Ipsum Door Sit...</h3>
    <p>Lorem ipsum dolor sit amet, consec-tetur adipiscing elit, sed do eiusmod tempor incididunt ut labore et...</p>
    <span class="read-more">Read More <svg width="13" height="8" viewBox="0 0 13 8"><path d="M0 4h11M8 1l3 3-3 3" fill="none" stroke="#33b8a4" stroke-width="1.4"/></svg></span>
  </article>
  <article class="blog-card" style="left:753px;top:524px">
    <div class="blog-media" role="img" aria-label="Illustration of a doctor presenting a reproductive health chart" style="background:linear-gradient(135deg,#dfe6fa,#c5d3f4)"></div>
    <h3>Lorem Ipsum Door Sit...</h3>
    <p>Lorem ipsum dolor sit amet, consec-tetur adipiscing elit, sed do eiusmod tempor incididunt ut labore et...</p>
    <span class="read-more">Read More <svg width="13" height="8" viewBox="0 0 13 8"><path d="M0 4h11M8 1l3 3-3 3" fill="none" stroke="#33b8a4" stroke-width="1.4"/></svg></span>
  </article>

  <div class="btn-pill" style="top:915px">See All Our Services</div>
</section>

<section class="education">
  <h2 class="section-title display" style="top:2289px">Educational Content</h2>
  <span class="title-rule" style="top:2347px"></span>

  <article class="edu-item" style="top:2387px">
    <svg class="edu-icon" width="74" height="90" viewBox="0 0 74 90"><path d="M4 2h48l20 20v64a2 2 0 0 1-2 2H4a2 2 0 0 1-2-2V4a2 2 0 0 1 2-2z" fill="#fff" stroke="#e0262b" stroke-width="3"/><path d="M52 2v20h20" fill="none" stroke="#e0262b" stroke-width="3"/><text x="37" y="74" text-anchor="middle" font-family="Montserrat,sans-serif" font-size="17" font-weight="500" fill="#222">PDF</text></svg>
    <span class="edu-divider" style="left:143px"></span>
    <span class="edu-date"><svg width="12" height="11" viewBox="0 0 12 11"><rect x=".5" y="1.5" width="11" height="9" fill="none" stroke="#33b8a4"/><rect x=".5" y="1.5" width="11" height="2.5" fill="#33b8a4"/></svg>Wed, 11 Nov 2020</span>
    <h4>Lorem ipsum carrots, enhanced...</h4>
    <p>Lorem ipsum carrots, enhanced undergraduate developer, but they do occaecat time and vitality, such...</p>
    <span class="edu-divider" style="left:541px"></span>
    <span class="edu-btn primary">Read More</span>
    <span class="edu-btn secondary">Download Pdf</span>
  </article>

  <article class="edu-item" style="top:2546px">
    <svg class="edu-icon" width="74" height="90" viewBox="0 0 74 90"><path d="M4 2h48l20 20v64a2 2 0 0 1-2 2H4a2 2 0 0 1-2-2V4a2 2 0 0 1 2-2z" fill="#fff" stroke="#e0262b" stroke-width="3"/><path d="M52 2v20h20" fill="none" stroke="#e0262b" stroke-width="3"/><text x="37" y="74" text-anchor="middle" font-family="Montserrat,sans-serif" font-size="17" font-weight="500" fill="#222">PDF</text></svg>
    <span class="edu-divider" style="left:143px"></span>
    <span class="edu-date"><svg width="12" height="11" viewBox="0 0 12 11"><rect x=".5" y="1.5" width="11" height="9" fill="none" stroke="#33b8a4"/><rect x=".5" y="1.5" width="11" height="2.5" fill="#33b8a4"/></svg>Wed, 11 Nov 2020</span>
    <h4>Lorem ipsum carrots, enhanced...</h4>
    <p>Lorem ipsum carrots, enhanced undergraduate developer, but they do occaecat time and vitality, such...</p>
    <span class="edu-divider" style="left:541px"></span>
    <span class="edu-btn primary">Read More</span>
    <span class="edu-btn secondary">Download Pdf</span>
  </article>

  <article class="edu-item" style="top:2704px">
    <svg class="edu-icon" width="74" height="90" viewBox="0 0 74 90"><path d="M4 2h48l20 20v64a2 2 0 0 1-2 2H4a2 2 0 0 1-2-2V4a2 2 0 0 1 2-2z" fill="#fff" stroke="#e0262b" stroke-width="3"/><path d="M52 2v20h20" fill="none" stroke="#e0262b" stroke-width="3"/><text x="37" y="74" text-anchor="middle" font-family="Montserrat,sans-serif" font-size="17" font-weight="500" fill="#222">PDF</text></svg>
    <span class="edu-divider" style="left:143px"></span>
    <span class="edu-date"><svg width="12" height="11" viewBox="0 0 12 11"><rect x=".5" y="1.5" width="11" height="9" fill="none" stroke="#33b8a4"/><rect x=".5" y="1.5" width="11" height="2.5" fill="#33b8a4"/></svg>Wed, 11 Nov 2020</span>
    <h4>Lorem ipsum carrots, enhanced...</h4>
    <p>Lorem ipsum carrots, enhanced undergraduate developer, but they do occaecat time and vitality, such...</p>
    <span class="edu-divider" style="left:541px"></span>
    <span class="edu-btn primary">Read More</span>
    <span class="edu-btn secondary">Download Pdf</span>
  </article>
</section>

<footer class="site-footer">
  <div class="footer-brand"><span class="brand-dot"></span>Grey Fennel Medical</div>
  <div class="lang-select"><span>English</span><svg width="7" height="5" viewBox="0 0 7 5"><path d="M0 0h7L3.5 5z" fill="#fff"/></svg></div>

  <h5 class="footer-heading" style="left:390px;top:73px">Quick Links</h5>
  <span class="footer-rule" style="left:390px;top:102px"></span>
  <ul class="footer-links">
    <li style="top:116px">Home</li>
    <li style="top:139px">Staff</li>
    <li style="top:161px">Services</li>
    <li style="top:184px">Contact Us</li>
    <li style="top:206px">Patients</li>
    <li style="top:229px">Health Professionals</li>
  </ul>

  <h5 class="footer-heading" style="left:560px;top:73px">Contact Us</h5>
  <span class="footer-rule" style="left:560px;top:102px"></span>
  <div class="contact-row" style="top:122px">
    <svg width="10" height="14" viewBox="0 0 10 14"><path d="M5 0a5 5 0 0 1 5 5c0 4-5 9-5 9S0 9 0 5a5 5 0 0 1 5-5z" fill="#fff"/><circle cx="5" cy="5" r="2" fill="#000"/></svg>
    <span>Grey Fennel Medical</span></div>
  <div class="contact-row" style="top:148px">
    <svg width="10" height="14" viewBox="0 0 9 15"><rect x=".7" y=".7" width="7.6" height="13.6" rx="1.5" fill="none" stroke="#fff" stroke-width="1.4"/></svg>
    <span><b>Call Us:</b><br>02987654310</span></div>
  <div class="contact-row" style="top:189px">
    <svg width="13" height="10" viewBox="0 0 15 11"><rect width="15" height="11" fill="#fff"/><path d="M0 0l7.5 6L15 0" fill="none" stroke="#000" stroke-width="1.2"/></svg>
    <span><b>Email.Us:</b><br>hello@greyfennelmed.com</span></div>

  <h5 class="footer-heading" style="left:773px;top:77px">Get Social</h5>
  <span class="footer-rule" style="left:773px;top:106px"></span>
  <span class="social-circle" style="left:771px" aria-label="Social link 1"></span>
  <span class="social-circle" style="left:813px" aria-label="Social link 2"></span>
  <span class="social-circle" style="left:856px" aria-label="Social link 3"></span>
  <span class="social-circle" style="left:898px" aria-label="Social link 4"></span>

  <span class="footer-base"></span>
  <p class="copyright" style="left:184px">Copyright © Grey Fennel Medical 2020. All right Reserved</p>
  <p class="copyright" style="right:184px">Privacy Policy, Disclaimer</p>
</footer>

</body>
</html>
```